Bramblewood Joinery Website

My client Bramblewood Joinery is looking for a redesign for a Word Press Website. Their current site is at www.bramblewoodjoinery.example They are a custom cabinet company, but also create bathroom, living room, bar and entertainment and bedroom cabinets too. They would like a design that emulates the master craftsman work they do yet a contemporary style.

Their current site was designed using Flash elements.

Target Market(s)

Home owners and builders of high end homes

Industry/Entity Type

Entertainment

Font styles to use
Serif
Decorative

Requirements
Must have
• Must show their work and logo using a contemporary style.
Nice to have
• Sliders that showcase their projects.

```html
<!DOCTYPE html>
<html lang="en">
<head>
<meta charset="utf-8">
<title>Bramblewood Joinery</title>
<link href="https://fonts.googleapis.com/css2?family=Open+Sans:ital,wght@0,400;0,600;1,400;1,600&family=Prata&family=Exo+2:wght@700&family=Kalam&family=Roboto+Condensed&display=swap" rel="stylesheet">
<style>
:root{
  --green:#2fae3a;
  --green-dark:#23862c;
  --text:#444;
  --muted:#8a8a8a;
  --dark:#2b2b2b;
  --wood-light:#c99464;
  --wood-dark:#8a5530;
  --footer-bg:#e6e6e6;
  --frame:#b8773f;
}
*{box-sizing:border-box;margin:0;padding:0}
html,body{width:970px;height:1200px;overflow:hidden;background:#fff}
body{position:relative;font-family:"Open Sans",sans-serif;color:var(--text)}
.abs{position:absolute}

/* header */
.brand{left:88px;top:10px;display:flex;align-items:center;gap:10px}
.brand-mark{width:70px;height:70px;border-radius:50%;background:var(--green)}
.brand-name{font-family:"Prata",serif;font-size:20px;color:var(--dark);width:140px;line-height:1.15}
.top-nav{left:415px;top:31px;display:flex;gap:20px;font-style:italic;font-size:12px;color:var(--muted)}
.phone{left:675px;top:28px;font-style:italic;font-weight:600;font-size:15px;color:var(--dark);display:flex;align-items:center;gap:6px}
.phone b{color:var(--green);font-weight:600}
.main-nav{left:415px;top:61px;display:flex;gap:0;font-style:italic;font-size:12px;color:#555}
.main-nav span{padding:0 14px;line-height:24px}
.main-nav .active{background:var(--green);color:#fff;padding:0 13px;font-weight:600;margin-right:2px}

/* slider */
.wood{left:0;top:114px;width:970px;height:290px}
.slide{background:#ccc}
.slide-caption{position:absolute;left:0;right:0;bottom:0;background:rgba(30,30,30,.78);color:#fff;font-family:"Prata",serif;display:flex;align-items:center}
.slide-caption em{font-style:normal;color:var(--green)}
.dots{position:absolute;right:12px;display:flex;gap:4px}
.dots i{width:7px;height:7px;border-radius:50%;background:#888}
.dots i:first-child{background:var(--green)}

/* info boxes */
.card{width:236px;height:206px;top:499px;background:linear-gradient(#fafafa,#e2e2e2);box-shadow:0 6px 8px -6px rgba(0,0,0,.35)}
.card-head{height:36px;background:linear-gradient(#555,#2a2a2a);color:#fff;font-family:"Prata",serif;font-size:17px;text-align:center;line-height:36px;border-bottom:2px solid var(--green);border-radius:0 0 50% 50%/0 0 8px 8px}
.card p{font-size:9.6px;line-height:14.5px;padding:10px 7px 0}
.card ul{font-size:9.6px;line-height:18px;padding:5px 0 0 36px;list-style:none}
.card li{position:relative}
.card li::before{content:"";position:absolute;left:-22px;top:7px;width:5px;height:5px;border-radius:50%;background:#333}
.btn-more{display:block;margin:8px auto 0;width:84px;height:23px;background:linear-gradient(#3bb548,var(--green-dark));color:#fff;font-size:10px;text-align:center;line-height:23px;border:1px solid #1d6e24}

/* gallery */
.gallery-title{left:96px;top:723px;font-family:"Prata",serif;font-size:17px;color:#111}
.thumb{top:762px;width:164px;height:126px;border:10px solid var(--frame);box-shadow:0 2px 3px rgba(0,0,0,.3);background:linear-gradient(135deg,#7a4a28,#d3a068 55%,#5a3a22)}

/* banner */
.banner{left:98px;top:913px;width:776px;height:80px;border:1px solid #dcdcdc;background:linear-gradient(90deg,#f2f8ef,#fff 60%);overflow:hidden}
.banner-photo{position:absolute;right:0;top:0;width:240px;height:100%;background:linear-gradient(90deg,rgba(255,255,255,1),rgba(176,120,70,.9) 45%,#7a5234)}
.banner-title{position:absolute;left:19px;top:10px;font-family:"Exo 2",sans-serif;font-size:25px;color:var(--green)}
.banner-note{position:absolute;left:336px;top:10px;font-family:"Kalam",cursive;font-size:17px;color:#c0392b}
.banner-text{position:absolute;left:21px;top:44px;font-family:"Roboto Condensed",sans-serif;font-size:18px;color:#555}
.order{position:absolute;left:556px;top:42px;width:88px;height:28px;border-radius:50%;background:radial-gradient(#f4e64a,#c8b400);font-size:11px;color:#222;text-align:center;line-height:28px;font-weight:600}

/* footer nav */
.footer-rule{left:0;top:1018px;width:970px;height:2px;background:#333}
.footer-nav{left:88px;top:1032px;display:flex;gap:22px;font-size:11.5px;color:#444}
.footer{left:0;top:1067px;width:970px;height:133px;background:var(--footer-bg)}
.socials{left:161px;top:1119px;display:flex;gap:6px}
.socials i{width:26px;height:26px;display:block}
.copy{left:88px;top:1161px;font-size:10.5px}
.nl-title{left:401px;top:1098px;font-size:15px;color:#555}
.nl-sub{left:402px;top:1120px;font-size:10.5px}
.email{left:402px;top:1146px;width:223px;height:28px;display:flex;background:#fff;border:1px solid #ccc}
.email b{background:var(--dark);color:#fff;font-weight:600;font-size:12px;width:62px;line-height:26px;text-align:center}
.email span{margin-left:auto;margin-right:6px;align-self:center}
.service{left:673px;top:1088px;font-size:10.5px;line-height:16px}
.contact{left:674px;top:1146px;display:flex;gap:3px}
.contact i{width:39px;height:28px;background:var(--dark);display:flex;align-items:center;justify-content:center}
.contact b{width:165px;height:28px;background:var(--dark);color:#fff;font-weight:600;font-size:14px;line-height:28px;padding-left:13px}
</style>
</head>
<body>

<header>
  <div class="abs brand"><span class="brand-mark"></span><span class="brand-name">Bramblewood Joinery</span></div>
  <nav class="abs top-nav"><span>Professional</span><span>Portfolio</span><span>Cabinet Hardware</span></nav>
  <div class="abs phone">
    <svg width="13" height="13" viewBox="0 0 24 24"><path fill="#555" d="M6.6 10.8a15 15 0 0 0 6.6 6.6l2.2-2.2c.3-.3.7-.4 1-.2 1.1.4 2.3.6 3.6.6.6 0 1 .4 1 1V20c0 .6-.4 1-1 1A17 17 0 0 1 3 4c0-.6.4-1 1-1h3.5c.6 0 1 .4 1 1 0 1.3.2 2.5.6 3.6.1.3 0 .7-.2 1z"/></svg>
    <span>Call Today..! <b>1-800-555-0142</b></span>
  </div>
  <nav class="abs main-nav"><span class="active">Home</span><span>Who We Are</span><span>Getting Started</span><span>Contact Us</span><span>Customer Experience</span></nav>
</header>

<svg class="abs wood" viewBox="0 0 970 290" role="img" aria-label="Warm wooden plank backdrop">
  <defs><linearGradient id="wd" x1="0" x2="1"><stop offset="0" stop-color="#9a6238"/><stop offset=".5" stop-color="#c99464"/><stop offset="1" stop-color="#9a6238"/></linearGradient></defs>
  <path d="M0 0H970V282Q485 170 0 282Z" fill="url(#wd)"/>
</svg>

<section class="slider">
  <div class="abs slide" style="left:96px;top:137px;width:225px;height:170px;background:linear-gradient(160deg,#e8e2d6,#b79a74)" role="img" aria-label="Finished bathroom with wooden vanity">
    <div class="slide-caption" style="height:32px;padding-left:13px;font-size:16px">Bramblewood&nbsp;<em>BATHROOM</em></div>
  </div>
  <div class="abs slide" style="left:96px;top:310px;width:225px;height:170px;background:linear-gradient(160deg,#9c958c,#5e4d3c)" role="img" aria-label="Video preview of a workshop office"></div>
  <div class="abs slide" style="left:324px;top:137px;width:550px;height:343px;background:linear-gradient(170deg,#d8b27e,#a66e3a 55%,#5b4032)" role="img" aria-label="Kitchen with honey oak cabinets and granite island">
    <div class="slide-caption" style="height:44px;padding-left:13px;font-size:17px">Welcome To&nbsp;<em>BRAMBLEWOOD JOINERY</em><span class="dots"><i></i><i></i><i></i><i></i></span></div>
  </div>
</section>

<section class="cards">
  <article class="abs card" style="left:97px"><h2 class="card-head">Who We Are</h2>
    <p>Lorem ipsum dolor sit amet, consectetuer adipiscing elit, sed diam nonummy nibh euismod tincidunt ut laoreet dolore magna aliquam erat</p>
    <ul><li>Ut wisi enim ad minim veniam, quis</li><li>nostrud exerci tation ullamcorper suscipit</li><li>lobortis nisl ut aliquip ex ea commodo</li></ul>
    <span class="btn-more">read more</span></article>
  <article class="abs card" style="left:368px"><h2 class="card-head">Design Services</h2>
    <p>Lorem ipsum dolor sit amet, consectetuer adipiscing elit, sed diam nonummy nibh euismod tincidunt ut laoreet dolore magna aliquam erat</p>
    <ul><li>Ut wisi enim ad minim veniam, quis</li><li>nostrud exerci tation ullamcorper suscipit</li><li>lobortis nisl ut aliquip ex ea commodo</li></ul>
    <span class="btn-more">read more</span></article>
  <article class="abs card" style="left:638px"><h2 class="card-head">About Us</h2>
    <p>Lorem ipsum dolor sit amet, consectetuer adipiscing elit, sed diam nonummy nibh euismod tincidunt ut laoreet dolore magna aliquam erat</p>
    <ul><li>Ut wisi enim ad minim veniam, quis</li><li>nostrud exerci tation ullamcorper suscipit</li><li>lobortis nisl ut aliquip ex ea commodo</li></ul>
    <span class="btn-more">read more</span></article>
</section>

<section class="gallery">
  <h2 class="abs gallery-title">PHOTO GALLERY</h2>
  <div class="abs thumb" style="left:96px" role="img" aria-label="Dining room with built-in hutch"></div>
  <div class="abs thumb" style="left:301px" role="img" aria-label="Dark wood kitchen with island"></div>
  <div class="abs thumb" style="left:504px" role="img" aria-label="Rustic kitchen with stone backsplash"></div>
  <div class="abs thumb" style="left:709px" role="img" aria-label="Kitchen with maple cabinets and sink"></div>
</section>

<section class="abs banner">
  <div class="banner-photo" role="img" aria-label="Kitchen cabinets beside a steel refrigerator"></div>
  <div class="banner-title">Perfect Fit Guarantee</div>
  <svg class="abs" style="left:286px;top:20px" width="38" height="16" viewBox="0 0 38 16"><path d="M2 8H34M26 2L34 8L26 14" stroke="var(--green)" stroke-width="2" fill="none"/></svg>
  <div class="banner-note">for a free!</div>
  <div class="banner-text">For a fee we will come measure the kitchen and guarantee a perfect fit.</div>
  <div class="order">Order Now</div>
</section>

<footer>
  <div class="abs footer-rule"></div>
  <svg class="abs" style="left:98px;top:1019px" width="10" height="7"><path d="M0 0H10L5 7Z" fill="#333"/></svg>
  <nav class="abs footer-nav"><span>Home</span><span>Who We Are</span><span>Getting Started</span><span>Contact Us</span><span>Customer Experience</span><span>Professional</span><span>Portfolio</span><span>Cabinet Hardware</span></nav>
  <div class="abs footer"></div>
  <div class="abs socials"><i style="background:#3b5998"></i><i style="background:#333"></i><i style="background:#cb2027"></i><i style="background:#2fa8e0"></i></div>
  <div class="abs copy">Copyrights © 2015 Bramblewood.example - All Rights Reserved</div>
  <div class="abs nl-title">Newsletter</div>
  <div class="abs nl-sub">Join us to start receiving news about new</div>
  <div class="abs email"><b>Email</b><span><svg width="18" height="18" viewBox="0 0 18 18"><circle cx="9" cy="9" r="8" fill="none" stroke="#666" stroke-width="1.5"/><path d="M5 9H12M9 6L12 9L9 12" stroke="#666" stroke-width="1.5" fill="none"/></svg></span></div>
  <div class="abs service">Service Centers<br>88 Alder Lane, Suite 12 - 40<br>Millbrook 5521</div>
  <div class="abs contact"><i><svg width="14" height="14" viewBox="0 0 24 24"><path fill="#fff" d="M6.6 10.8a15 15 0 0 0 6.6 6.6l2.2-2.2c.3-.3.7-.4 1-.2 1.1.4 2.3.6 3.6.6.6 0 1 .4 1 1V20c0 .6-.4 1-1 1A17 17 0 0 1 3 4c0-.6.4-1 1-1h3.5c.6 0 1 .4 1 1 0 1.3.2 2.5.6 3.6.1.3 0 .7-.2 1z"/></svg></i><b>Contact Us Today..!</b></div>
</footer>

</body>
</html>
```